Business Card for beauty technology startup

Design Glimora Business Card for a Beauty, based on the website identity and colors (https://www.glimora-example.com).
Glimora is a beauty tech startup that gathers helpful product info for beauty lovers and consumers (such as availability on stores, price range and product reviews) for makeup products. The card design must be young, colorful but clean, and very modern.

Target Market(s)

woman, 15-35

Industry/Entity Type

Cosmetics

Contact Information for Business Card

Full Name, address, phone

Font styles to use
Other font styles liked:
• Advent Pro

Colors
e34297
86cfc6
ffffff
5c5c5c
e8e8e8
e667a6
b2b2b2

Requirements
Must have
• One full colored side with a creative design and another with card info
• Use Color palette: #95C5C5 and/or #D38AA5
• Use fonts: Advent Pro
• Use website identity: https://www.glimora-example.com
Nice to have
• If needed extra font: Roboto

```html
<!DOCTYPE html>
<html lang="en">
<head>
<meta charset="utf-8">
<title>Glimora Business Card</title>
<link href="https://fonts.googleapis.com/css2?family=Advent+Pro:wght@300;600&family=Roboto:wght@400&display=swap" rel="stylesheet">
<style>
  :root {
    --backdrop: #e6e6e6;
    --card-top: #cd8299;
    --card-bottom: #b9758f;
    --ink-dark: #2e2a2c;
    --ink-light: #ffffff;
    --rule: rgba(255, 255, 255, 0.45);
  }
  * { margin: 0; padding: 0; box-sizing: border-box; }
  html, body {
    width: 1200px;
    height: 576px;
    overflow: hidden;
    background: var(--backdrop);
  }
  .canvas {
    position: relative;
    width: 1200px;
    height: 576px;
  }
  .card {
    position: absolute;
    top: 138px;
    width: 484px;
    height: 294px;
    border-radius: 13px;
    background: linear-gradient(180deg, var(--card-top) 0%, var(--card-bottom) 100%);
  }
  .card--front { left: 82px; }
  .card--back { left: 602px; }

  .brand {
    position: absolute;
    left: 0;
    right: 0;
    top: 120px;
    display: flex;
    align-items: center;
    justify-content: center;
    gap: 16px;
  }
  .brand__dot {
    width: 40px;
    height: 40px;
    border: 1.5px solid var(--ink-dark);
    border-radius: 50%;
  }
  .brand__name {
    font-family: "Advent Pro", sans-serif;
    font-weight: 300;
    font-size: 46px;
    letter-spacing: 5px;
    color: var(--ink-dark);
    line-height: 1;
  }

  .contact {
    position: absolute;
    left: 0;
    right: 0;
    top: 88px;
    text-align: center;
    color: var(--ink-light);
  }
  .contact__name {
    font-family: "Advent Pro", sans-serif;
    font-weight: 600;
    font-size: 21px;
    letter-spacing: 0.5px;
    line-height: 24px;
    margin-bottom: 7px;
  }
  .contact__line {
    font-family: "Roboto", sans-serif;
    font-size: 11.5px;
    line-height: 16.5px;
  }
  .contact__rule {
    width: 324px;
    height: 1px;
    margin: 6px auto 5px;
    background: var(--rule);
  }
</style>
</head>
<body>
<main class="canvas">
  <section class="card card--front" aria-label="Card front">
    <div class="brand">
      <span class="brand__dot"></span>
      <span class="brand__name">GLIMORA</span>
    </div>
  </section>

  <section class="card card--back" aria-label="Card back">
    <div class="contact">
      <p class="contact__name">MARA ELLISON</p>
      <p class="contact__line">00 444 555 666</p>
      <p class="contact__line">yourname@glimora-example.com</p>
      <p class="contact__line">www.glimora-example.com</p>
      <div class="contact__rule"></div>
      <p class="contact__line">123, Street Number, City Name, Country - 123456</p>
    </div>
  </section>
</main>
</body>
</html>
```